Construction company that specializes in roofing and siding

https://maplecrestbuild.example/featured-projects/

https://www.bramwickhomesllc.example/#

https://www.tallgrovecontractors.example/residential-siding-services/

Please model a website after these examples
I posted a doc that has some content to get you started. I will upload more content and photos as the site progresses.

Coded - Design and coding required

5+ page

```html
<!DOCTYPE html>
<html lang="en">
<head>
<meta charset="utf-8">
<title>Stoneridge Construction</title>
<link href="https://fonts.googleapis.com/css2?family=Poppins:ital,wght@0,400;0,500;0,600;0,700;0,800;1,600&display=swap" rel="stylesheet">
<style>
:root{
  --slate:#37414f;
  --slate-dark:#2b333e;
  --ink:#151a21;
  --text:#4a4f57;
  --mist:#f3f3f3;
  --line:#d9dde3;
  --teal:#2f5d55;
  --quote:#a9b4c4;
  --star:#e6b422;
  --footer:#1d1f23;
  --white:#fff;
}
*{box-sizing:border-box;margin:0;padding:0}
html,body{width:1200px;height:4938px;overflow:hidden}
body{font-family:"Poppins",sans-serif;color:var(--text);background:var(--white);position:relative}
h1,h2,h3{font-family:"Poppins",sans-serif;color:var(--ink);font-weight:800}

/* header */
.site-header{position:absolute;top:0;left:0;width:1200px;height:80px;z-index:5}
.brand{position:absolute;left:96px;top:26px;display:flex;align-items:center;gap:10px;font-weight:700;font-size:19px;letter-spacing:1px;color:var(--slate-dark)}
.brand .mark{width:30px;height:30px;background:var(--slate-dark)}
.nav-bar{position:absolute;left:336px;top:15px;width:864px;height:56px;background:rgba(214,228,245,.85);clip-path:polygon(28px 0,100% 0,100% 100%,28px 100%,0 50%)}
.nav-bar ul{list-style:none;display:flex;position:absolute;left:26px;top:0;height:56px;align-items:center;font-size:10.5px;color:var(--ink);white-space:nowrap}
.nav-bar li{padding:0 11px}
.nav-bar li.active{position:relative}
.nav-bar li.active:after{content:"";position:absolute;left:11px;right:11px;bottom:-20px;height:2px;background:var(--slate)}
.btn-contact{position:absolute;left:628px;top:8px;width:142px;height:40px;background:var(--slate);color:#fff;font-size:11px;font-weight:600;display:flex;align-items:center;justify-content:center;outline:1px solid var(--slate);outline-offset:3px}

/* hero */
.hero{position:absolute;top:0;left:0;width:1200px;height:652px;background:linear-gradient(180deg,#7fa8e0 0%,#a9c3e6 35%,#c9c9c6 55%,#6f6b63 80%,#4c5a3a 100%)}
.hero-text{position:absolute;top:126px;left:0;width:1200px;text-align:center}
.hero-text .eyebrow{font-size:16px;font-weight:600;color:var(--ink)}
.hero-text h1{font-size:44px;line-height:1.1;margin-top:4px}
.hero-text h1 span{color:#3d4654;background:linear-gradient(transparent 55%,rgba(170,185,205,.8) 55%)}
.hero-text p{font-size:11px;color:var(--ink);width:620px;margin:10px auto 0;line-height:1.5}
.btn-dark{display:inline-flex;align-items:center;justify-content:center;background:var(--slate);color:#fff;font-size:11px;font-weight:600;outline:1px solid var(--slate);outline-offset:3px}
.hero-text .btn-dark{width:142px;height:40px;margin-top:28px}
.dots{position:absolute;display:flex;gap:6px;z-index:3}
.dots i{width:7px;height:7px;border-radius:50%;background:#fff;opacity:.8}

/* contact */
.contact-frame{position:absolute;left:182px;top:600px;width:840px;height:236px;border:1px solid #9aa2ad}
.contact-box{position:absolute;left:196px;top:585px;width:812px;height:240px;background:var(--slate);z-index:2}
.contact-box h2{color:#fff;font-size:24px;text-align:center;margin-top:34px}
.field{position:absolute;background:#fff;font-size:10px;color:#666;padding:12px 16px}
.submit{position:absolute;left:654px;top:92px;width:104px;height:98px;background:#fff;outline:1px solid #fff;outline-offset:3px;display:flex;flex-direction:column;align-items:center;justify-content:center;gap:8px;font-size:10px;font-weight:700;color:var(--slate)}

/* about */
.about h2{position:absolute;left:96px;top:955px;font-size:42px;line-height:1.15}
.about .copy{position:absolute;left:96px;top:1070px;width:400px;font-size:11px;line-height:1.6;color:var(--text)}
.about .copy p{margin-bottom:14px}
.about .copy .pull{font-size:14px;color:var(--ink);font-weight:500;line-height:1.5}
.signature{position:absolute;left:86px;top:1362px;width:210px;height:40px;background:linear-gradient(90deg,#e8eaed,#f7f7f7)}
.about-photo{position:absolute;left:560px;top:935px;width:640px;height:500px;background:linear-gradient(135deg,#3b3f45 0%,#2c3036 40%,#8a6a4a 70%,#c3a27c 100%)}
.about-frame{position:absolute;left:566px;top:941px;width:634px;height:488px;border:1px solid #fff}

/* services */
.services-band{position:absolute;left:0;top:1530px;width:1200px;height:464px;background:var(--mist)}
.section-title{position:absolute;left:0;width:1200px;text-align:center;font-size:40px}
.card{position:absolute;background:#fff;box-shadow:0 4px 14px rgba(0,0,0,.08)}
.service-card{top:1693px;width:255px;height:387px}
.service-card .photo{position:absolute;left:12px;top:0;width:233px;height:263px}
.service-card h3{position:absolute;left:20px;top:280px;font-size:17px}
.service-card p{position:absolute;left:20px;top:310px;width:215px;font-size:9.5px;line-height:1.6}
.arrow-box{position:absolute;width:26px;height:24px;background:#eef0f2;display:flex;align-items:center;justify-content:center}
.slider-arrow{position:absolute}

/* why */
.why-card{width:188px;height:157px;background:#fff;box-shadow:0 4px 16px rgba(0,0,0,.07)}
.why-card svg{position:absolute;left:16px;top:30px}
.why-card h3{position:absolute;left:16px;top:104px;font-size:11.5px;font-weight:600;line-height:1.35;width:160px}

/* testimonials */
.testimonial{position:absolute;top:2678px;width:410px}
.testimonial .q{width:60px;height:60px;background:var(--quote);display:flex;align-items:center;justify-content:center}
.testimonial .rule{position:absolute;left:68px;top:56px;width:310px;height:3px;background:var(--teal)}
.testimonial blockquote{margin-top:22px;font-size:13.5px;font-style:italic;font-weight:600;color:var(--ink);line-height:1.75}
.person{display:flex;align-items:center;gap:10px;margin-top:22px;position:relative}
.avatar{width:42px;height:42px;background:linear-gradient(135deg,#c9d3c0,#8ca0b6)}
.person b{display:block;font-size:12px;color:var(--ink)}
.person small{font-size:9px}
.stars{position:absolute;right:30px;top:12px;color:var(--star);font-size:14px;letter-spacing:1px}
.dots-dark i{background:#c8ccd2}
.dots-dark i.on{width:18px;border-radius:4px;background:var(--teal)}

.roof-banner{position:absolute;left:0;top:2960px;width:1200px;height:284px;background:linear-gradient(180deg,#fff 0%,#fff 45%,#3f6b78 62%,#1f3d4a 100%)}

/* work */
.work-intro{position:absolute;left:330px;top:3380px;width:540px;text-align:center;font-size:11px;line-height:1.7}
.work-card{top:3470px;width:389px;height:383px;background:transparent;box-shadow:none}
.work-card .ba{position:absolute;left:0;top:0;width:389px;height:240px}
.work-card .divider{position:absolute;left:194px;top:0;width:3px;height:240px;background:#fff}
.work-card .knob{position:absolute;left:184px;top:108px;width:23px;height:23px;border-radius:50%;background:#fff}
.work-card .body{position:absolute;left:10px;top:240px;width:369px;height:143px;background:#fff;box-shadow:0 6px 16px rgba(0,0,0,.08)}
.work-card h3{position:absolute;left:22px;top:26px;font-size:17px;line-height:1.3;width:330px}
.work-card p{position:absolute;left:22px;top:82px;width:300px;font-size:9.5px;line-height:1.6}

/* request */
.request-photo{position:absolute;left:0;top:3953px;width:1200px;height:615px;background:linear-gradient(180deg,#dfe3e8 0%,#c7ccd3 45%,#6f7379 75%,#3e4146 100%)}
.request-frame{position:absolute;left:753px;top:4033px;width:338px;height:440px;border:2px solid var(--slate)}
.request-box{position:absolute;left:765px;top:4045px;width:312px;height:427px;background:var(--slate)}
.request-box h2{color:#fff;font-size:33px;text-align:center;margin-top:26px}
.request-box .field{left:30px;width:252px;height:42px}
.request-box .btn{position:absolute;left:30px;top:375px;width:252px;height:36px;background:#fff;outline:1px solid #fff;outline-offset:3px;font-size:11px;font-weight:700;color:var(--slate);display:flex;align-items:center;justify-content:center}

/* footer */
.site-footer{position:absolute;left:0;top:4568px;width:1200px;height:370px;background:var(--footer);color:#c9ccd1}
.site-footer .brand{left:90px;top:72px;color:#fff}
.site-footer .brand .mark{background:#fff}
.social{position:absolute;left:90px;top:148px;display:flex;gap:10px}
.social span{width:36px;height:36px;border:1px solid #6b7079}
.foot-col{position:absolute;top:78px;font-size:11px;line-height:1.75}
.foot-col h4{color:#fff;font-size:12px;font-weight:700;margin-bottom:6px}
.foot-col .row{display:flex;gap:8px;margin-bottom:10px}
.foot-col .row b{color:#fff;font-weight:600}
.map{position:absolute;left:767px;top:0;width:433px;height:292px;background:linear-gradient(135deg,#e9ecef,#d7e4ea 50%,#cfe0d4)}
.legal{position:absolute;left:0;top:292px;width:1200px;height:78px;background:#fff;font-size:10px;color:var(--ink)}
.legal .copy{position:absolute;left:94px;top:32px}
.legal .links{position:absolute;right:94px;top:32px;display:flex;gap:24px}
</style>
</head>
<body>

<section class="hero" role="img" aria-label="Photo of a large white two-storey house with dark shingle roof at dusk"></section>

<header class="site-header">
  <div class="brand"><span class="mark"></span>STONERIDGE</div>
  <nav class="nav-bar">
    <ul>
      <li class="active">Home</li><li>About</li><li>Roofing ⌄</li><li>Siding ⌄</li><li>Gutters</li><li>Windows</li><li>Repair ⌄</li><li>Storm Damage ⌄</li>
    </ul>
    <div class="btn-contact">CONTACT US</div>
  </nav>
</header>

<div class="hero-text">
  <div class="eyebrow">THE FLEXIBLE</div>
  <h1>OPTION FOR YOUR <span>CLEANUP</span></h1>
  <p>In 2016 Eli Marsh started helping people with their home improvement projects. His very first job was installing window trim for a wonderful homeowner in Forest lake MN.</p>
  <div class="btn-dark">SCHEDULE NOW</div>
</div>
<div class="dots" style="left:575px;top:556px"><i></i><i></i><i></i><i></i></div>

<div class="contact-frame"></div>
<section class="contact-box">
  <h2>CONTACT US</h2>
  <div class="field" style="left:52px;top:92px;width:190px;height:42px">Name</div>
  <div class="field" style="left:252px;top:92px;width:190px;height:42px">Email</div>
  <div class="field" style="left:52px;top:148px;width:190px;height:42px">Phone</div>
  <div class="field" style="left:252px;top:148px;width:190px;height:42px">Address</div>
  <div class="field" style="left:452px;top:92px;width:190px;height:98px">Message</div>
  <div class="submit">
    <svg width="34" height="30" viewBox="0 0 34 30"><path d="M2 14 32 2 24 28 16 18Z" fill="none" stroke="#37414f" stroke-width="2.5" stroke-linejoin="round"/><path d="M16 18 32 2" stroke="#37414f" stroke-width="2"/></svg>
    SUBMIT NOW
  </div>
</section>

<section class="about">
  <h2>ABOUT<br>STONERIDGE</h2>
  <div class="copy">
    <p>From humble beginnings:</p>
    <p>In 2016 Eli Marsh started helping people with their home improvement projects. His very first job was installing window trim for a wonderful homeowner in Forest lake MN. He did his best work and made sure he treated his first customer like family. Afterall, his first customer was Rosa Marsh, his Mom.</p>
    <p>Today, Eli and the Stoneridge Construction team are helping homeowners around Minnesota; carrying the spirit of his first job onto every job they touch.</p>
    <p class="pull">“We are helping a lot more people now, but we haven't lost the dedication to service and craftsmanship that I had on my very first job.”</p>
  </div>
  <div class="signature" role="img" aria-label="Handwritten signature of the owner"></div>
  <div class="about-photo" role="img" aria-label="Two roofers in hard hats installing dark metal roof panels on a timber-clad house"></div>
  <div class="about-frame"></div>
</section>

<div class="services-band"></div>
<h2 class="section-title" style="top:1602px">SERVICES WE PROVIDE</h2>
<svg class="slider-arrow" style="left:92px;top:1853px" width="30" height="16" viewBox="0 0 30 16"><path d="M29 8H2M9 1 2 8l7 7" fill="none" stroke="#aab0b8" stroke-width="2"/></svg>
<svg class="slider-arrow" style="left:1076px;top:1853px" width="30" height="16" viewBox="0 0 30 16"><path d="M1 8h27M21 1l7 7-7 7" fill="none" stroke="#151a21" stroke-width="2"/></svg>

<article class="card service-card" style="left:194px">
  <div class="photo" role="img" aria-label="Roofer in hard hat and safety vest laying grey shingles" style="background:linear-gradient(160deg,#9fc4e6,#6a7078 45%,#4d545c)"></div>
  <h3>ROOFING</h3>
  <p>At Stoneridge Construction we specialize in replacing architectural shingle roofing.</p>
  <div class="arrow-box" style="left:218px;top:349px"><svg width="12" height="8" viewBox="0 0 12 8"><path d="M0 4h10M7 1l3 3-3 3" fill="none" stroke="#151a21" stroke-width="1.3"/></svg></div>
</article>
<article class="card service-card" style="left:473px">
  <div class="photo" role="img" aria-label="Gable of a house with new wood-tone siding and dark roof" style="background:linear-gradient(160deg,#dfe6ee,#b98a58 55%,#5b4a3a)"></div>
  <h3>SIDING</h3>
  <p>A typical vinyl siding replacement can be completed in 3-5 days.</p>
  <div class="arrow-box" style="left:218px;top:349px"><svg width="12" height="8" viewBox="0 0 12 8"><path d="M0 4h10M7 1l3 3-3 3" fill="none" stroke="#151a21" stroke-width="1.3"/></svg></div>
</article>
<article class="card service-card" style="left:753px">
  <div class="photo" role="img" aria-label="Black seamless gutter and downspout on beige siding" style="background:linear-gradient(160deg,#6a6e74,#c9bba5 45%,#a89a86)"></div>
  <h3>GUTTERS</h3>
  <p>We offer 5" or 6" aluminum seamless gutters for your home or business.</p>
  <div class="arrow-box" style="left:218px;top:349px"><svg width="12" height="8" viewBox="0 0 12 8"><path d="M0 4h10M7 1l3 3-3 3" fill="none" stroke="#151a21" stroke-width="1.3"/></svg></div>
</article>

<h2 class="section-title" style="top:2198px">WHT CHOOSE US</h2>

<div class="card why-card" style="left:200px;top:2287px">
  <svg width="70" height="44" viewBox="0 0 70 44" fill="none" stroke="#37414f" stroke-width="2"><path d="M12 8h30v24H12zM42 16h12l8 10v6H42z"/><circle cx="20" cy="36" r="5"/><circle cx="52" cy="36" r="5"/><path d="M2 14h8M0 20h10M4 26h6"/></svg>
  <h3>Including delivery, collection &amp; disposal</h3>
</div>
<div class="card why-card" style="left:408px;top:2287px">
  <svg width="50" height="50" viewBox="0 0 50 50" fill="none" stroke="#37414f" stroke-width="2"><path d="M8 4h26l6 6v36H8z"/><circle cx="24" cy="16" r="5"/><path d="M16 30h16M16 36h12"/><path d="M38 24 46 16"/></svg>
  <h3>Aggregates for any application</h3>
</div>
<div class="card why-card" style="left:619px;top:2287px">
  <svg width="70" height="46" viewBox="0 0 70 46" fill="none" stroke="#37414f" stroke-width="2"><circle cx="14" cy="12" r="10"/><path d="M14 6v6l4 3"/><path d="M26 14h18v20H26zM44 20h10l8 8v6H44z"/><circle cx="32" cy="38" r="4"/><circle cx="54" cy="38" r="4"/></svg>
  <h3>Fast, easy online ordering</h3>
</div>
<div class="card why-card" style="left:828px;top:2287px">
  <svg width="50" height="50" viewBox="0 0 50 50" fill="none" stroke="#37414f" stroke-width="2"><path d="M8 4h24l6 6v36H8z"/><path d="M14 16h16M14 22h16M14 28h10"/><path d="M44 18 28 38l-4 2 1-4 16-20z"/></svg>
  <h3>Report missed pickups online</h3>
</div>
<div class="card why-card" style="left:200px;top:2469px">
  <svg width="64" height="46" viewBox="0 0 64 46" fill="none" stroke="#37414f" stroke-width="2"><circle cx="16" cy="12" r="7"/><circle cx="48" cy="12" r="7"/><circle cx="32" cy="20" r="7"/><path d="M4 36c0-8 6-12 12-12M60 36c0-8-6-12-12-12M18 44c0-9 6-14 14-14s14 5 14 14"/></svg>
  <h3>Communications on your terms</h3>
</div>
<div class="card why-card" style="left:408px;top:2469px">
  <svg width="50" height="50" viewBox="0 0 50 50" fill="none" stroke="#37414f" stroke-width="2"><path d="M10 2h26v44H10z"/><path d="M16 10h14M16 16h14M16 22h14"/><circle cx="30" cy="34" r="6"/><path d="M27 34l2 2 4-4"/></svg>
  <h3>Fully insured and licensed</h3>
</div>
<div class="card why-card" style="left:619px;top:2469px">
  <svg width="60" height="50" viewBox="0 0 60 50" fill="none" stroke="#37414f" stroke-width="2"><circle cx="30" cy="22" r="5"/><circle cx="14" cy="28" r="4"/><circle cx="46" cy="28" r="4"/><path d="M20 48c0-8 4-14 10-14s10 6 10 14M6 46c0-6 3-10 8-10M54 46c0-6-3-10-8-10"/><path d="M30 2l2 4 4 1-3 3 1 4-4-2-4 2 1-4-3-3 4-1z"/></svg>
  <h3>We Value Our Customers</h3>
</div>
<div class="card why-card" style="left:828px;top:2469px">
  <svg width="50" height="50" viewBox="0 0 50 50" fill="none" stroke="#37414f" stroke-width="2"><circle cx="25" cy="22" r="18"/><circle cx="25" cy="18" r="5"/><path d="M16 32c2-6 6-8 9-8s7 2 9 8"/><path d="M10 44l6-6M40 44l-6-6"/></svg>
  <h3>We Value Inclusion &amp; Diversity</h3>
</div>

<article class="testimonial" style="left:194px">
  <div class="q"><svg width="30" height="22" viewBox="0 0 30 22" fill="#fff"><path d="M0 22V12L6 0h6L8 10h5v12zM17 22V12L23 0h6l-4 10h5v12z"/></svg></div>
  <div class="rule"></div>
  <blockquote>“Lorem ipsum dolor sit amet, consetetur adiscing elit, sed esmod tempor incididunt ut labore dolore magna aliqua. Quis ipsum sunisse ultrices gravida. Ris comodo viverra maecenas apumsan.”</blockquote>
  <div class="person"><div class="avatar" role="img" aria-label="Customer portrait"></div><div><b>Nora Vale</b><small>New york</small></div><span class="stars">★★★★★</span></div>
</article>
<article class="testimonial" style="left:633px">
  <div class="q"><svg width="30" height="22" viewBox="0 0 30 22" fill="#fff"><path d="M0 22V12L6 0h6L8 10h5v12zM17 22V12L23 0h6l-4 10h5v12z"/></svg></div>
  <div class="rule"></div>
  <blockquote>“Sed euismod hendrerit aliqet. Maecenas semper metus dui, rhoncus lorem malesuada. Vestibulum dictum hend rerit ante, suscipit metus consequat eget. Praesent portti tor vel justo id dignissim.”</blockquote>
  <div class="person"><div class="avatar" role="img" aria-label="Customer portrait"></div><div><b>Owen Pike</b><small>New york</small></div><span class="stars">★★★★★</span></div>
</article>

<div class="roof-banner" role="img" aria-label="Roofer with a power drill working on blue-green tile roof"></div>
<div class="dots dots-dark" style="left:566px;top:2949px"><i></i><i class="on"></i><i></i><i></i></div>

<h2 class="section-title" style="top:3300px">SEE OUR WORK</h2>
<p class="work-intro">Your home matters too much to trust just anyone with your exterior home remodel. Explore some of the results we've helped other customers achieve — we're sure the before and afters will speak for themselves.</p>
<svg class="slider-arrow" style="left:92px;top:3635px" width="30" height="16" viewBox="0 0 30 16"><path d="M29 8H2M9 1 2 8l7 7" fill="none" stroke="#aab0b8" stroke-width="2"/></svg>
<svg class="slider-arrow" style="left:1076px;top:3635px" width="30" height="16" viewBox="0 0 30 16"><path d="M1 8h27M21 1l7 7-7 7" fill="none" stroke="#151a21" stroke-width="2"/></svg>

<article class="card work-card" style="left:194px">
  <div class="ba" role="img" aria-label="Before and after photos of a lakeside cabin with new tile roof" style="background:linear-gradient(180deg,#c9d6e2,#8e9a7e 60%,#5d6b3e)"></div>
  <div class="divider"></div><div class="knob"></div>
  <div class="body">
    <h3>SOLANA CLAY BARREL TILE ROOF ON GULL LAKE</h3>
    <p>A cute cabin nestled on Gull Lake in Nisswa, MN was in need of a new roof...</p>
    <div class="arrow-box" style="left:331px;top:104px"><svg width="12" height="8" viewBox="0 0 12 8"><path d="M0 4h10M7 1l3 3-3 3" fill="none" stroke="#151a21" stroke-width="1.3"/></svg></div>
  </div>
</article>
<article class="card work-card" style="left:621px">
  <div class="ba" role="img" aria-label="Before and after photos of a brick family home with a new slate-style roof" style="background:linear-gradient(180deg,#c6d4e3,#8c7262 50%,#5e9a3a)"></div>
  <div class="divider"></div><div class="knob"></div>
  <div class="body">
    <h3>NORTHLINE RIDGE SLATE HARBOR GREY IN PELLA</h3>
    <p>A family home in Pella Iowa, had previously worked with another contractor and had their insurance claim...</p>
    <div class="arrow-box" style="left:331px;top:104px"><svg width="12" height="8" viewBox="0 0 12 8"><path d="M0 4h10M7 1l3 3-3 3" fill="none" stroke="#151a21" stroke-width="1.3"/></svg></div>
  </div>
</article>

<div class="request-photo" role="img" aria-label="Two roofers in hard hats fitting a vent pipe on a shingle roof"></div>
<div class="request-frame"></div>
<section class="request-box">
  <h2>REQUSET INFO</h2>
  <div class="field" style="top:90px">Full Name</div>
  <div class="field" style="top:146px">Email</div>
  <div class="field" style="top:202px">Phone Number</div>
  <div class="field" style="top:258px;height:98px">Full Name</div>
  <div class="btn">SCHEDULE NOW</div>
</section>

<footer class="site-footer">
  <div class="brand"><span class="mark"></span>STONERIDGE</div>
  <div class="social">
    <span role="img" aria-label="Social profile link"></span><span role="img" aria-label="Social profile link"></span><span role="img" aria-label="Social profile link"></span><span role="img" aria-label="Video channel link"></span>
  </div>
  <div class="foot-col" style="left:376px">
    <h4>NAVIGATION</h4>
    <div>» Roofing</div><div>» Siding</div><div>» Gutters</div><div>» Windows</div><div>» Repair</div><div>» Storm Damage</div>
  </div>
  <div class="foot-col" style="left:545px;width:210px">
    <h4>CONTACT INFO</h4>
    <div class="row"><svg width="10" height="14" viewBox="0 0 10 14"><path d="M5 13S1 8 1 5a4 4 0 0 1 8 0c0 3-4 8-4 8z" fill="#c9ccd1"/></svg><span>Address line come here,<br>Lorem ipsum, 123 456.</span></div>
    <div class="row"><svg width="12" height="12" viewBox="0 0 12 12"><path d="M2 1l2 0 1 3-1 1c1 2 2 3 3 3l1-1 3 1v2c-5 1-10-4-9-9z" fill="#c9ccd1"/></svg><span>Phone:<br><b>+123 456 7890</b></span></div>
    <div class="row"><svg width="12" height="10" viewBox="0 0 12 10"><rect x=".5" y=".5" width="11" height="9" fill="none" stroke="#c9ccd1"/><path d="M1 1l5 4 5-4" fill="none" stroke="#c9ccd1"/></svg><span>Email:<br><b>info@stoneridgebuild.example</b></span></div>
  </div>
  <div class="map" role="img" aria-label="Map showing the Stoneridge office location among lakes"></div>
  <div class="legal">
    <div class="copy">Copyright © 2024 <b>Stoneridge</b> | All rights reserved.</div>
    <div class="links"><span>Privacy Policy</span><span>|</span><span>Terms of Conditins</span></div>
  </div>
</footer>

</body>
</html>
```